Popcorn, ice cream, alcohol infused shakes shop

Create a clean simple website with pictures and bold type for a popcorn, ice cream and boozy shake shop. The site should have:
- Unique and Large Typography
- Large & Responsive Hero (stunning, elicits a response) Images.No concern with above or below the fold. Create a strong visual experience that encourages visitors to scroll down to read more. Use large images to visually tell a story without having to rely on just text.
- Flat image designs
- Place for me to upload an ad type video
- Hidden type menu (three line menu)
- A few small card like images (food, gift bags, tins, etc.) menu items with a brief description.

Target Market(s)

21-49 years of age for the boozy shakes. Soccer moms for sports teams & sleepovers, professionals (teachers, realtors, pharm sales), gifts for family and friends. Also some kids

Coding

Coded - Design and coding required

Number of Pages Required

5+ page

Font styles to use
Sans Serif

Colors

Designer to choose colors to be used in the design.

Requirements
Must have
• Images of gourmet popcorn, fancy shakes, ice cream, gift bags and popcorn tins. Holiday popcorn tins and gift bags along with grift certificates. Ability for visitors to send a contact form to kt@treatloft.example
• Five pages - Home Page, AboutUs, Menu, Gift/Promotion, Contact Us
Nice to have
• Smooth flow on the home page. Mostly images and bold text.
Should not have
• Too many words. Boring text fonts

```html
<!DOCTYPE html>
<html lang="en">
<head>
<meta charset="utf-8">
<title>Treat Loft – Home</title>
<link href="https://fonts.googleapis.com/css2?family=Oswald:wght@500;600;700&family=Montserrat:wght@400;500;600;700;800&display=swap" rel="stylesheet">
<style>
:root{
  --board:#efefef;
  --white:#ffffff;
  --ink:#2b2b2b;
  --muted:#555555;
  --purple:#5d479c;
  --green:#7cc242;
  --red:#d8262c;
  --link:#3a5bb0;
  --footer:#3a3a3a;
  --footer-bar:#2c2c2c;
  --panel:#f4f4f4;
}
*{box-sizing:border-box;margin:0;padding:0}
html,body{width:1200px;height:3138px;overflow:hidden}
body{background:var(--board);font-family:'Montserrat',sans-serif;color:var(--ink);position:relative}
.abs{position:absolute}
.brand-mark{left:67px;top:80px;font-family:'Oswald',sans-serif;font-weight:700;font-size:78px;line-height:.92;color:var(--purple);text-transform:uppercase;text-align:center;width:232px}
.frame{position:absolute;background:var(--white);overflow:hidden}
.frame--desktop{left:364px;top:77px;width:743px;height:2975px}
.frame--mobile{left:93px;top:284px;width:193px;height:2359px}
.logo-small{font-family:'Oswald',sans-serif;font-weight:700;color:var(--purple);line-height:.9;text-transform:uppercase}
.menu-icons{display:flex;gap:6px;align-items:center}
.headline{font-family:'Oswald',sans-serif;font-weight:700;text-transform:uppercase;line-height:1;color:var(--ink);white-space:nowrap}
.headline--green{color:var(--green)}
.center{left:0;right:0;text-align:center}
.lede{color:var(--muted)}
.btn{display:flex;align-items:center;justify-content:center;background:var(--purple);color:var(--white);font-weight:500}
.btn--light{background:var(--white);color:var(--ink);font-weight:600}
.photo{position:absolute}
/* soft tonal fills standing in for food photography */
.pop{background:radial-gradient(circle at 55% 30%,#fbf1cf 0%,#f0d68a 30%,transparent 60%),linear-gradient(180deg,#6a4a2c 0%,#e7c76f 35%,#f6f1ea 60%,#d2282c 80%,#f3e9e2 100%)}
.sprinkle{background:radial-gradient(circle at 45% 45%,#fdf7ee 0%,#f1d9de 35%,transparent 65%),linear-gradient(135deg,#2c1f18 0%,#6a5046 30%,#e9c9a0 70%,#c88a4d 100%)}
.shake{background:radial-gradient(circle at 42% 48%,#b69ad6 0%,#8e6bb9 30%,transparent 55%),radial-gradient(circle at 82% 70%,#cfe27a 0%,transparent 30%),linear-gradient(160deg,#2a211d 0%,#5d4638 60%,#3b2d25 100%)}
.tart{background:radial-gradient(ellipse at 45% 40%,#f7c6d3 0%,#ec9fb5 35%,transparent 65%),linear-gradient(160deg,#f2e2cf 0%,#e8b8a8 50%,#9c3f43 80%,#efd8c4 100%)}
.drink{background:radial-gradient(circle at 55% 55%,#f4a046 0%,#c0461b 35%,transparent 65%),linear-gradient(135deg,#1c0d08 0%,#7a2410 40%,#e39a3c 70%,#2a1308 100%)}
.gift{background:radial-gradient(ellipse at 45% 55%,#e3b878 0%,#c6914e 40%,transparent 70%),linear-gradient(135deg,#f7f4ef 0%,#d6a869 35%,#b07b3c 70%,#f2eee8 100%)}
.cone{background:radial-gradient(circle at 45% 32%,#f6c9d9 0%,#ee9dbd 25%,transparent 45%),radial-gradient(circle at 78% 70%,#f8f5ee 0%,#e8e3d9 18%,transparent 34%),radial-gradient(ellipse at 40% 70%,#e2368a 0%,#cf2f7e 20%,transparent 40%),radial-gradient(ellipse at 85% 92%,#9ccc3f 0%,transparent 35%),linear-gradient(180deg,#efe4ea 0%,#ead8e0 55%,#c89a7c 100%)}
.sundae{background:radial-gradient(closest-side at 50% 50%,#d32f3a 0%,#d32f3a 7%,#faf7f2 9%,#f2ece4 30%,#c9a184 48%,#7d5a44 66%,rgba(93,71,156,0) 100%)}
.fire{background:radial-gradient(ellipse at 50% 30%,#f5b04a 0%,#d2601c 22%,transparent 45%),radial-gradient(ellipse at 65% 75%,#c11e24 0%,#8e1518 35%,transparent 60%),linear-gradient(180deg,#2a1208 0%,#3b1609 50%,#2a0b0b 100%)}
.card{position:absolute}
.card .photo{position:relative}
.card-desc{color:var(--ink)}
.price-row{display:flex;align-items:center}
.price{font-weight:700;color:var(--ink)}
.old{color:var(--red);text-decoration:line-through;font-weight:500}
.add{margin-left:auto;display:flex;align-items:center;justify-content:center;background:var(--purple);color:var(--white);font-weight:500}
.frame--desktop .card{width:198px}
.frame--desktop .card .photo{height:156px}
.frame--desktop .card-desc{font-size:10.5px;line-height:13px;margin-top:12px;font-weight:500}
.frame--desktop .price-row{margin-top:10px;height:28px}
.frame--desktop .price{font-size:25px}
.frame--desktop .old{font-size:8px;margin-left:8px}
.frame--desktop .add{width:52px;height:22px;font-size:10px;gap:4px}
.frame--mobile .card{width:83px}
.frame--mobile .card .photo{height:65px}
.frame--mobile .card-desc{font-size:5px;line-height:7px;margin-top:5px}
.frame--mobile .price-row{margin-top:6px;height:10px}
.frame--mobile .price{font-size:7.5px}
.frame--mobile .add{width:32px;height:8px;font-size:4px;gap:2px}
.band{position:absolute;left:0;right:0;background:var(--purple)}
.special-title{font-family:'Oswald',sans-serif;font-weight:600;color:var(--white);line-height:1.02;white-space:nowrap}
.special-text{color:var(--white);font-weight:600}
.articles{position:absolute;background:var(--panel)}
.articles h3{font-weight:700;color:var(--muted)}
.article-date{font-weight:700;color:var(--ink)}
.article-title{color:var(--ink);font-weight:500}
.read-more{color:var(--link);font-weight:600;display:flex;align-items:center;gap:6px;text-transform:uppercase;letter-spacing:.5px}
.rule{height:1px;background:#dcdcdc}
.footer{position:absolute;left:0;right:0;background:var(--footer);color:var(--white)}
.footer-bar{position:absolute;left:0;right:0;background:var(--footer-bar);color:#bdbdbd;text-align:center}
.footer h4{font-weight:700}
.footer-links{list-style:none;color:#cfcfcf}
.field{position:absolute;border:1px solid #8a8a8a;color:#a8a8a8;padding:2px 5px}
.send{position:absolute;background:var(--purple);color:var(--white);display:flex;align-items:center;justify-content:center}
.social{display:flex}
.social span{display:block;border-radius:50%;background:var(--white)}
.dots{display:flex;align-items:center;justify-content:center;gap:4px}
.dot{border-radius:50%;background:#c2c2c2}
.dot--on{background:#333}
</style>
</head>
<body>

<div class="abs brand-mark">Treat<br>Loft</div>

<main class="frame frame--mobile">
  <div class="abs logo-small" style="left:11px;top:9px;font-size:10px">Treat<br>Loft</div>
  <div class="photo cone" role="img" aria-label="Ice cream cups with sprinkles and chocolate" style="left:99px;top:0;width:94px;height:179px"></div>
  <div class="abs menu-icons" style="left:158px;top:15px">
    <svg width="10" height="8" viewBox="0 0 10 8"><path d="M0 1h10M0 4h10M0 7h10" stroke="#222" stroke-width="1.4"/></svg>
    <svg width="8" height="8" viewBox="0 0 8 8"><circle cx="3.3" cy="3.3" r="2.5" fill="none" stroke="#222" stroke-width="1"/><path d="M5 5l2.5 2.5" stroke="#222" stroke-width="1"/></svg>
  </div>
  <div class="abs headline" style="left:11px;top:138px;font-size:29px">We Are</div>
  <div class="abs headline headline--green" style="left:11px;top:169px;font-size:37px">Food</div>
  <div class="abs headline" style="left:11px;top:207px;font-size:37px">Masters</div>
  <p class="abs lede" style="left:11px;top:260px;width:150px;font-size:8px;line-height:14px">Lorem Ipsum Is Simply Dummy Text Of The Printing And Typesetting Industry.</p>
  <div class="abs btn" style="left:11px;top:321px;width:76px;height:21px;font-size:6px">Order Now</div>
  <div class="abs dots" style="left:50px;top:370px;width:90px">
    <svg width="12" height="6" viewBox="0 0 12 6"><path d="M12 3H1M3.5 .5L1 3l2.5 2.5" fill="none" stroke="#333" stroke-width=".9"/></svg>
    <span class="dot" style="width:3px;height:3px"></span><span class="dot dot--on" style="width:4px;height:4px"></span><span class="dot" style="width:3px;height:3px"></span>
    <svg width="12" height="6" viewBox="0 0 12 6"><path d="M0 3h11M8.5 .5L11 3 8.5 5.5" fill="none" stroke="#333" stroke-width=".9"/></svg>
  </div>

  <div class="abs headline center" style="top:416px;font-size:38px">Deals And</div>
  <div class="abs headline headline--green center" style="top:456px;font-size:38px">Offers</div>

  <article class="card" style="left:11px;top:530px"><div class="photo pop" role="img" aria-label="Striped box of popcorn"></div><p class="card-desc">Save 25% on optional burger from Café Lindell</p><div class="price-row"><span class="price">$87.00</span><span class="add">Add</span></div></article>
  <article class="card" style="left:98px;top:530px"><div class="photo sprinkle" role="img" aria-label="Ice cream cone with rainbow sprinkles"></div><p class="card-desc">Save 25% on optional burger from Café Lindell</p><div class="price-row"><span class="price">$87.00</span><span class="add">Add</span></div></article>
  <article class="card" style="left:11px;top:643px"><div class="photo shake" role="img" aria-label="Berry shake with lime"></div><p class="card-desc">Save 25% on optional burger from Café Lindell</p><div class="price-row"><span class="price">$87.00</span><span class="add">Add</span></div></article>
  <article class="card" style="left:98px;top:643px"><div class="photo tart" role="img" aria-label="Frosted pastry with sprinkles"></div><p class="card-desc">Save 25% on optional burger from Café Lindell</p><div class="price-row"><span class="price">$87.00</span><span class="add">Add</span></div></article>
  <article class="card" style="left:11px;top:755px"><div class="photo drink" role="img" aria-label="Iced cocktail glasses"></div><p class="card-desc">Save 25% on optional burger from Café Lindell</p><div class="price-row"><span class="price">$87.00</span><span class="add">Add</span></div></article>
  <article class="card" style="left:98px;top:755px"><div class="photo gift" role="img" aria-label="Kraft paper gift bags of popcorn"></div><p class="card-desc">Save 25% on optional burger from Café Lindell</p><div class="price-row"><span class="price">$87.00</span><span class="add">Add</span></div></article>

  <section class="band" style="top:930px;height:309px"></section>
  <div class="photo sundae" role="img" aria-label="Ice cream sundae with wafer rolls and a cherry" style="left:72px;top:880px;width:150px;height:160px"></div>
  <h2 class="abs special-title" style="left:11px;top:1060px;font-size:29px">Today’s Special<br>Food</h2>
  <p class="abs special-text" style="left:11px;top:1137px;width:150px;font-size:7.5px;line-height:10px">Energistically negotiate stand-alone infomediaries rather than ubiquitous</p>
  <div class="abs btn btn--light" style="left:11px;top:1186px;width:76px;height:21px;font-size:6px">Shop Now</div>

  <div class="abs headline center" style="top:1279px;font-size:38px">Most</div>
  <div class="abs headline headline--green center" style="top:1318px;font-size:38px">Popular</div>

  <article class="card" style="left:11px;top:1391px;width:76px"><div class="photo tart" style="height:58px" role="img" aria-label="Frosted pastry with sprinkles"></div><p class="card-desc">Save 25% on optional burger from Café Lindell</p><div class="price-row"><span class="price">$87.00</span><span class="add">Add</span></div></article>
  <article class="card" style="left:92px;top:1391px;width:76px"><div class="photo drink" style="height:58px" role="img" aria-label="Iced cocktail glasses"></div><p class="card-desc">Save 25% on optional burger from Café Lindell</p><div class="price-row"><span class="price">$87.00</span><span class="add">Add</span></div></article>
  <article class="card" style="left:173px;top:1391px;width:76px"><div class="photo gift" style="height:58px" role="img" aria-label="Kraft paper gift bags of popcorn"></div><p class="card-desc">Save 25% on optional burger from Café Lindell</p><div class="price-row"><span class="price">$87.00</span><span class="add">Add</span></div></article>

  <section class="articles" style="left:11px;top:1531px;width:170px;height:351px">
    <h3 class="abs" style="left:9px;top:14px;font-size:11px">Articles</h3>
    <div class="photo fire" role="img" aria-label="Popcorn bowl and mug by a fireplace" style="left:9px;top:41px;width:153px;height:132px;border-radius:9px"></div>
    <p class="abs article-date" style="left:9px;top:196px;font-size:6px">27.02.2019</p>
    <p class="abs article-title" style="left:9px;top:206px;width:150px;font-size:7.5px;line-height:10px">Uniquely synthesize error-free experiences</p>
    <p class="abs read-more" style="left:9px;top:234px;font-size:6px">Read More <svg width="12" height="6" viewBox="0 0 12 6"><path d="M0 3h11M8.5 .5L11 3 8.5 5.5" fill="none" stroke="#3a5bb0" stroke-width=".9"/></svg></p>
    <div class="abs rule" style="left:9px;top:252px;width:140px"></div>
    <p class="abs article-date" style="left:9px;top:275px;font-size:6px">27.02.2019</p>
    <p class="abs article-title" style="left:9px;top:285px;width:150px;font-size:7.5px;line-height:10px">Uniquely synthesize error-free experiences</p>
    <p class="abs read-more" style="left:9px;top:313px;font-size:6px">Read More <svg width="12" height="6" viewBox="0 0 12 6"><path d="M0 3h11M8.5 .5L11 3 8.5 5.5" fill="none" stroke="#3a5bb0" stroke-width=".9"/></svg></p>
  </section>

  <footer class="footer" style="top:1923px;height:400px">
    <h4 class="abs center" style="top:27px;font-size:10px">Treat Loft</h4>
    <ul class="abs footer-links center" style="top:53px;font-size:6px;line-height:15.5px">
      <li>Home</li><li>About Us</li><li>Menu</li><li>Gift/Promotion</li><li>Contact Us</li>
    </ul>
    <h4 class="abs center" style="top:150px;font-size:10px">Contact Us</h4>
    <span class="field" style="left:17px;top:180px;width:76px;height:14px;font-size:5px">Name*</span>
    <span class="field" style="left:98px;top:180px;width:76px;height:14px;font-size:5px">Email*</span>
    <span class="field" style="left:17px;top:200px;width:76px;height:14px;font-size:5px">Phone No.</span>
    <span class="field" style="left:98px;top:200px;width:76px;height:14px;font-size:5px">Address</span>
    <span class="field" style="left:17px;top:219px;width:157px;height:53px;font-size:5px">Message</span>
    <span class="send" style="left:56px;top:285px;width:79px;height:24px;font-size:6px">Send</span>
    <h4 class="abs center" style="top:330px;font-size:9px">Follow Us</h4>
    <div class="abs social" style="left:64px;top:352px;gap:5px" aria-label="Social links">
      <span style="width:18px;height:18px"></span><span style="width:18px;height:18px"></span><span style="width:18px;height:18px"></span>
    </div>
  </footer>
  <div class="footer-bar" style="top:2323px;height:36px;line-height:36px;font-size:5.5px">Treat Loft Copyright © 2019</div>
</main>

<main class="frame frame--desktop">
  <div class="abs logo-small" style="left:81px;top:12px;font-size:20px">Treat<br>Loft</div>
  <div class="photo cone" role="img" aria-label="Pink and vanilla ice cream cups with sprinkles, chocolate and wafers" style="left:400px;top:0;width:343px;height:432px"></div>
  <div class="abs menu-icons" style="left:632px;top:23px">
    <svg width="14" height="11" viewBox="0 0 14 11"><path d="M0 1.5h14M0 5.5h14M0 9.5h14" stroke="#222" stroke-width="2"/></svg>
    <svg width="11" height="11" viewBox="0 0 11 11"><circle cx="4.5" cy="4.5" r="3.5" fill="none" stroke="#222" stroke-width="1.3"/><path d="M7 7l3.5 3.5" stroke="#222" stroke-width="1.3"/></svg>
  </div>
  <div class="abs headline" style="left:82px;top:99px;font-size:62px">We Are</div>
  <div class="abs headline headline--green" style="left:82px;top:164px;font-size:76px">Food</div>
  <div class="abs headline" style="left:82px;top:243px;font-size:76px">Masters</div>
  <p class="abs lede" style="left:82px;top:340px;width:300px;font-size:11.5px;line-height:19px">Lorem Ipsum Is Simply Dummy Text Of The Printing And Typesetting Industry.</p>
  <div class="abs btn" style="left:82px;top:393px;width:103px;height:26px;font-size:8px">Order Now</div>
  <div class="abs dots" style="left:272px;top:462px;width:200px;gap:9px">
    <svg width="20" height="10" viewBox="0 0 20 10"><path d="M20 5H1.5M5.5 1L1.5 5l4 4" fill="none" stroke="#333" stroke-width="1.3"/></svg>
    <span class="dot" style="width:6px;height:6px"></span><span class="dot dot--on" style="width:8px;height:8px"></span><span class="dot" style="width:6px;height:6px"></span>
    <svg width="20" height="10" viewBox="0 0 20 10"><path d="M0 5h18.5M14.5 1l4 4-4 4" fill="none" stroke="#333" stroke-width="1.3"/></svg>
  </div>

  <h2 class="abs headline center" style="top:532px;font-size:82px">Deals And</h2>
  <div class="abs headline headline--green center" style="top:612px;font-size:82px">Offers</div>

  <article class="card" style="left:62px;top:744px"><div class="photo pop" role="img" aria-label="Striped box of popcorn"></div><p class="card-desc">Save 25% on optional burger<br>from Café Lindell</p><div class="price-row"><span class="price">$87.00</span><span class="old">$93.00</span><span class="add"><svg width="10" height="9" viewBox="0 0 10 9"><path d="M0 1h2l1.3 5h5L9.5 2.5H2.6" fill="none" stroke="#fff" stroke-width=".9"/><circle cx="4" cy="7.8" r=".8" fill="#fff"/><circle cx="7.5" cy="7.8" r=".8" fill="#fff"/></svg>Add</span></div></article>
  <article class="card" style="left:273px;top:744px"><div class="photo sprinkle" role="img" aria-label="Ice cream cone with rainbow sprinkles"></div><p class="card-desc">Save 25% on optional burger<br>from Café Lindell</p><div class="price-row"><span class="price">$87.00</span><span class="old">$93.00</span><span class="add"><svg width="10" height="9" viewBox="0 0 10 9"><path d="M0 1h2l1.3 5h5L9.5 2.5H2.6" fill="none" stroke="#fff" stroke-width=".9"/><circle cx="4" cy="7.8" r=".8" fill="#fff"/><circle cx="7.5" cy="7.8" r=".8" fill="#fff"/></svg>Add</span></div></article>
  <article class="card" style="left:484px;top:744px"><div class="photo shake" role="img" aria-label="Berry shake with lime and mint"></div><p class="card-desc">Save 25% on optional burger<br>from Café Lindell</p><div class="price-row"><span class="price">$87.00</span><span class="old">$93.00</span><span class="add"><svg width="10" height="9" viewBox="0 0 10 9"><path d="M0 1h2l1.3 5h5L9.5 2.5H2.6" fill="none" stroke="#fff" stroke-width=".9"/><circle cx="4" cy="7.8" r=".8" fill="#fff"/><circle cx="7.5" cy="7.8" r=".8" fill="#fff"/></svg>Add</span></div></article>
  <article class="card" style="left:62px;top:1007px"><div class="photo tart" role="img" aria-label="Frosted pastry with sprinkles"></div><p class="card-desc">Save 25% on optional burger<br>from Café Lindell</p><div class="price-row"><span class="price">$87.00</span><span class="old">$93.00</span><span class="add"><svg width="10" height="9" viewBox="0 0 10 9"><path d="M0 1h2l1.3 5h5L9.5 2.5H2.6" fill="none" stroke="#fff" stroke-width=".9"/><circle cx="4" cy="7.8" r=".8" fill="#fff"/><circle cx="7.5" cy="7.8" r=".8" fill="#fff"/></svg>Add</span></div></article>
  <article class="card" style="left:273px;top:1007px"><div class="photo drink" role="img" aria-label="Iced cocktail glasses"></div><p class="card-desc">Save 25% on optional burger<br>from Café Lindell</p><div class="price-row"><span class="price">$87.00</span><span class="old">$93.00</span><span class="add"><svg width="10" height="9" viewBox="0 0 10 9"><path d="M0 1h2l1.3 5h5L9.5 2.5H2.6" fill="none" stroke="#fff" stroke-width=".9"/><circle cx="4" cy="7.8" r=".8" fill="#fff"/><circle cx="7.5" cy="7.8" r=".8" fill="#fff"/></svg>Add</span></div></article>
  <article class="card" style="left:484px;top:1007px"><div class="photo gift" role="img" aria-label="Kraft paper gift bags of popcorn"></div><p class="card-desc">Save 25% on optional burger<br>from Café Lindell</p><div class="price-row"><span class="price">$87.00</span><span class="old">$93.00</span><span class="add"><svg width="10" height="9" viewBox="0 0 10 9"><path d="M0 1h2l1.3 5h5L9.5 2.5H2.6" fill="none" stroke="#fff" stroke-width=".9"/><circle cx="4" cy="7.8" r=".8" fill="#fff"/><circle cx="7.5" cy="7.8" r=".8" fill="#fff"/></svg>Add</span></div></article>

  <section class="band" style="top:1311px;height:334px"></section>
  <div class="photo sundae" role="img" aria-label="Ice cream sundae with wafer rolls, cookies and a cherry" style="left:480px;top:1280px;width:320px;height:380px"></div>
  <h2 class="abs special-title" style="left:62px;top:1360px;font-size:64px">Today’s Special<br>Food</h2>
  <p class="abs special-text" style="left:62px;top:1503px;width:340px;font-size:12.5px;line-height:16px">Energistically negotiate stand-alone infomediaries rather than ubiquitous</p>
  <div class="abs btn btn--light" style="left:62px;top:1553px;width:89px;height:28px;font-size:9.5px">Shop Now</div>

  <h2 class="abs headline center" style="top:1708px;font-size:82px">Most</h2>
  <div class="abs headline headline--green center" style="top:1788px;font-size:82px">Popular</div>

  <article class="card" style="left:62px;top:1922px"><div class="photo tart" role="img" aria-label="Frosted pastry with sprinkles"></div><p class="card-desc">Save 25% on optional burger<br>from Café Lindell</p><div class="price-row"><span class="price">$87.00</span><span class="old">$93.00</span><span class="add"><svg width="10" height="9" viewBox="0 0 10 9"><path d="M0 1h2l1.3 5h5L9.5 2.5H2.6" fill="none" stroke="#fff" stroke-width=".9"/><circle cx="4" cy="7.8" r=".8" fill="#fff"/><circle cx="7.5" cy="7.8" r=".8" fill="#fff"/></svg>Add</span></div></article>
  <article class="card" style="left:273px;top:1922px"><div class="photo drink" role="img" aria-label="Iced cocktail glasses"></div><p class="card-desc">Save 25% on optional burger<br>from Café Lindell</p><div class="price-row"><span class="price">$87.00</span><span class="old">$93.00</span><span class="add"><svg width="10" height="9" viewBox="0 0 10 9"><path d="M0 1h2l1.3 5h5L9.5 2.5H2.6" fill="none" stroke="#fff" stroke-width=".9"/><circle cx="4" cy="7.8" r=".8" fill="#fff"/><circle cx="7.5" cy="7.8" r=".8" fill="#fff"/></svg>Add</span></div></article>
  <article class="card" style="left:484px;top:1922px"><div class="photo gift" role="img" aria-label="Kraft paper gift bags of popcorn"></div><p class="card-desc">Save 25% on optional burger<br>from Café Lindell</p><div class="price-row"><span class="price">$87.00</span><span class="old">$93.00</span><span class="add"><svg width="10" height="9" viewBox="0 0 10 9"><path d="M0 1h2l1.3 5h5L9.5 2.5H2.6" fill="none" stroke="#fff" stroke-width=".9"/><circle cx="4" cy="7.8" r=".8" fill="#fff"/><circle cx="7.5" cy="7.8" r=".8" fill="#fff"/></svg>Add</span></div></article>

  <svg class="abs" style="left:340px;top:2192px" width="64" height="30" viewBox="0 0 64 30">
    <circle cx="15" cy="15" r="14" fill="#2b2b2b"/><path d="M17 10l-5 5 5 5" fill="none" stroke="#fff" stroke-width="2"/>
    <circle cx="49" cy="15" r="14" fill="#2b2b2b"/><path d="M47 10l5 5-5 5" fill="none" stroke="#fff" stroke-width="2"/>
  </svg>

  <section class="articles" style="left:62px;top:2257px;width:619px;height:394px">
    <h3 class="abs" style="left:26px;top:36px;font-size:20px">Articles</h3>
    <div class="photo fire" role="img" aria-label="Bowl of popcorn and a mug beside a fireplace" style="left:26px;top:86px;width:303px;height:263px;border-radius:14px"></div>
    <p class="abs article-date" style="left:48px;top:288px;font-size:11px;color:#fff">27.02.2019</p>
    <p class="abs article-title" style="left:48px;top:305px;width:260px;font-size:14px;line-height:19px;color:#fff">Uniquely synthesize error-free experiences</p>
    <p class="abs article-date" style="left:350px;top:116px;font-size:12px">27.02.2019</p>
    <p class="abs article-title" style="left:350px;top:135px;width:240px;font-size:15px;line-height:20px">Uniquely synthesize error-free experiences</p>
    <p class="abs read-more" style="left:350px;top:187px;font-size:13px">Read More <svg width="22" height="10" viewBox="0 0 22 10"><path d="M0 5h20M16 1l4 4-4 4" fill="none" stroke="#3a5bb0" stroke-width="1.3"/></svg></p>
    <div class="abs rule" style="left:350px;top:222px;width:245px"></div>
    <p class="abs article-date" style="left:350px;top:255px;font-size:12px">27.02.2019</p>
    <p class="abs article-title" style="left:350px;top:274px;width:240px;font-size:15px;line-height:20px">Uniquely synthesize error-free experiences</p>
    <p class="abs read-more" style="left:350px;top:326px;font-size:13px">Read More <svg width="22" height="10" viewBox="0 0 22 10"><path d="M0 5h20M16 1l4 4-4 4" fill="none" stroke="#3a5bb0" stroke-width="1.3"/></svg></p>
  </section>

  <footer class="footer" style="top:2717px;height:222px">
    <div class="abs" style="left:261px;top:0;width:1px;height:222px;background:#4a4a4a"></div>
    <div class="abs" style="left:485px;top:0;width:1px;height:222px;background:#4a4a4a"></div>
    <h4 class="abs" style="left:0;width:227px;text-align:right;top:33px;font-size:11px">Treat Loft</h4>
    <ul class="abs footer-links" style="left:0;width:227px;text-align:right;top:60px;font-size:7px;line-height:16px">
      <li>Home</li><li>About Us</li><li>Menu</li><li>Gift/Promotion</li><li>Contact Us</li>
    </ul>
    <h4 class="abs" style="left:262px;width:223px;text-align:center;top:33px;font-size:11px">Contact Us</h4>
    <span class="field" style="left:294px;top:62px;width:76px;height:15px;font-size:5.5px">Name*</span>
    <span class="field" style="left:374px;top:62px;width:76px;height:15px;font-size:5.5px">Email*</span>
    <span class="field" style="left:294px;top:82px;width:76px;height:15px;font-size:5.5px">Phone No.</span>
    <span class="field" style="left:374px;top:82px;width:76px;height:15px;font-size:5.5px">Address</span>
    <span class="field" style="left:294px;top:101px;width:156px;height:53px;font-size:5.5px">Message</span>
    <span class="send" style="left:333px;top:167px;width:79px;height:24px;font-size:7px">Send</span>
    <h4 class="abs" style="left:523px;top:33px;font-size:11px">Follow Us</h4>
    <div class="abs social" style="left:523px;top:67px;gap:8px" aria-label="Social links">
      <span style="width:22px;height:22px"></span><span style="width:22px;height:22px"></span><span style="width:22px;height:22px"></span>
    </div>
  </footer>
  <div class="footer-bar" style="top:2939px;height:36px;line-height:36px;font-size:6.5px">Treat Loft Copyright © 2019</div>
</main>

</body>
</html>
```